Professional violinist needs business cards

I am trying to attract the following jobs:
-private violin lessons (primarily classical)
-performance gigs (weddings, birthday parties, funerals, etc.)
-collaborations with other artists (studio recordings, performances)

I want to communicate that I have a very high standard of excellence for my work, but I also love people and celebrations.
Values/style words I like are:
love, joy, peace, fun, beauty, authenticity, excellence, warmth, refined/sleek, free spirited. If that's too confusing, just ignore :)

I will attach my favorite business card template that I could find on Canva. The lines are supposed to be like a music staff, which I think is really cool, but I also don't want it to look too busy. I like the simple black and white--I think it looks sharp--but I also am open to other ideas. I also have seen business cards with pictures included that looked great, so I attached an image that could be used as well.

I am also attaching a file that I made of my initials that could be used as a logo, but I'm not sure if it should be included.

Information on the card:
-My name (18 letters total)
-"violinist"
-phone number, email, website

Thank you!

```html
<!DOCTYPE html>
<html lang="en">
<head>
<meta charset="utf-8">
<title>Helena Marwick – Violinist Business Card</title>
<link href="https://fonts.googleapis.com/css2?family=Dancing+Script:wght@500&family=Cinzel:wght@400&family=Lora:wght@400;500&display=swap" rel="stylesheet">
<style>
  :root {
    --backdrop: #2b2b2c;
    --card: #22252a;
    --card-edge: #1d2024;
    --gold: #cdb690;
    --ink-light: #e6e4df;
    --ink-soft: #d8d6d0;
    --staff-line: #3a3e44;
    --watermark: rgba(255, 255, 255, 0.06);
    --photo-stone: #6e6658;
    --photo-dark: #2c2a27;
  }
  * { box-sizing: border-box; margin: 0; padding: 0; }
  html, body {
    width: 1200px; height: 1138px; overflow: hidden;
    background: var(--backdrop);
  }
  .card {
    position: absolute;
    width: 620px; height: 375px;
    background: linear-gradient(180deg, #272a2f 0%, var(--card) 60%, var(--card-edge) 100%);
    border-radius: 14px;
    overflow: hidden;
  }
  .card--front { left: 274px; top: 186px; }
  .card--back { left: 276px; top: 608px; }

  .staff { position: absolute; left: 0; top: 92px; width: 620px; height: 72px; }

  .watermark {
    position: absolute;
    border-radius: 45% 45% 40% 40%;
    background: radial-gradient(ellipse at center, var(--watermark) 0%, rgba(255,255,255,0.035) 55%, rgba(255,255,255,0) 75%);
  }
  .watermark--top-right { left: 536px; top: -6px; width: 96px; height: 176px; }
  .watermark--bottom-left { left: -8px; top: 150px; width: 100px; height: 232px; }

  .monogram {
    position: absolute;
    font-family: "Lora", serif;
    font-weight: 500;
    color: var(--gold);
    letter-spacing: 2px;
  }
  .card--front .monogram {
    left: 0; width: 620px; top: 100px;
    text-align: center; font-size: 58px; line-height: 1;
  }
  .card--back .monogram {
    right: 40px; top: 50px;
    font-size: 64px; line-height: 1;
  }

  .name {
    position: absolute; left: 0; width: 620px; top: 194px;
    text-align: center;
    font-family: "Dancing Script", cursive;
    font-weight: 500;
    font-size: 46px;
    line-height: 1.2;
    color: var(--ink-light);
  }
  .role {
    position: absolute; left: 0; width: 620px; top: 256px;
    text-align: center;
    font-family: "Cinzel", serif;
    font-size: 19px;
    letter-spacing: 3.5px;
    color: var(--ink-light);
  }

  .portrait {
    position: absolute; left: 0; top: 0;
    width: 255px; height: 375px;
    background: linear-gradient(160deg, var(--photo-stone) 0%, #5a5347 45%, var(--photo-dark) 100%);
  }

  .contact {
    position: absolute; right: 30px; top: 240px;
    list-style: none;
    font-family: "Lora", serif;
    font-size: 15px;
    color: var(--ink-soft);
  }
  .contact li {
    display: flex; justify-content: flex-end; align-items: center;
    height: 23.5px;
  }
  .contact svg { width: 13px; height: 13px; margin-left: 12px; fill: var(--ink-soft); }
  .contact .accent { color: var(--gold); }
</style>
</head>
<body>
  <section class="card card--front">
    <div class="watermark watermark--top-right" role="img" aria-label="Faint musical decoration in the top right corner"></div>
    <div class="watermark watermark--bottom-left" role="img" aria-label="Faint musical decoration in the bottom left corner"></div>
    <svg class="staff" viewBox="0 0 620 72" aria-hidden="true">
      <g stroke="var(--staff-line)" stroke-width="1.2">
        <line x1="0" y1="2" x2="620" y2="2"/>
        <line x1="0" y1="25" x2="620" y2="25"/>
        <line x1="0" y1="48" x2="620" y2="48"/>
        <line x1="0" y1="71" x2="620" y2="71"/>
      </g>
    </svg>
    <div class="monogram">HM</div>
    <h1 class="name">Helena Marwick</h1>
    <p class="role">VIOLINIST</p>
  </section>

  <section class="card card--back">
    <div class="portrait" role="img" aria-label="Portrait photo of the violinist holding her violin beside a stone wall"></div>
    <div class="monogram">HM</div>
    <ul class="contact">
      <li>+1 (555) 014-2290
        <svg viewBox="0 0 16 16" aria-hidden="true"><path d="M2 5c0-2 3-3 6-3s6 1 6 3v1h-3V5H5v1H2z M4 7h8l2 6H2z"/></svg>
      </li>
      <li>Helena@HelenaMarwick.com
        <svg viewBox="0 0 16 16" aria-hidden="true"><path d="M1 3h14v10H1z M2 4l6 5 6-5" fill="none" stroke="var(--ink-soft)" stroke-width="1.4"/></svg>
      </li>
      <li>www.<span class="accent">HelenaMarwick</span>.com
        <svg viewBox="0 0 16 16" aria-hidden="true"><g fill="none" stroke="var(--ink-soft)" stroke-width="1.2"><circle cx="8" cy="8" r="6.5"/><ellipse cx="8" cy="8" rx="3" ry="6.5"/><line x1="1.5" y1="8" x2="14.5" y2="8"/></g></svg>
      </li>
      <li>Portland, ME
        <svg viewBox="0 0 16 16" aria-hidden="true"><path d="M8 1a5 5 0 0 0-5 5c0 4 5 9 5 9s5-5 5-9a5 5 0 0 0-5-5zm0 7a2 2 0 1 1 0-4 2 2 0 0 1 0 4z"/></svg>
      </li>
    </ul>
  </section>
</body>
</html>
```